New website for out outstanding veterinary training center

We already have a beautiful logo with nice colors and we are now looking for a breathtaking modern website to present our training center and future corses held there. A section to book open courses should also be available.

We are planing the realize the website with Wordpress.
The following pages should be available:
- Startpage / Overview
- Page to present the different rooms and seating option
- Page where the rooms can be booked
- Page where recommended accommodation are presented
- Page to present and book corses
- contact page
- Impressum

Target Market(s)

European Union

Industry/Entity Type

Education, Veterinary medicine

Number of Pages Required

5+ page

Font styles to use
Sans Serif

Colors
00AB8E
00BBA5
67D7C9
C6EFE9
E9F9F6

Requirements
Must have
• The website must be clear and easy to read. The colors form the logos should be used for the design.
Should not have
• To playful design. The page is not for a veterinary practice. we are a training center for veterinarians!

```html
<!DOCTYPE html>
<html lang="en">
<head>
<meta charset="utf-8">
<title>Veterra Training Center</title>
<link href="https://fonts.googleapis.com/css2?family=Lato:wght@400;700;900&display=swap" rel="stylesheet">
<style>
:root{
  --teal:#00AB8E;
  --teal-2:#1aae98;
  --teal-dark:#1b8277;
  --mint:#b8ebe4;
  --mint-pale:#E9F9F6;
  --ink:#3f2f3a;
  --plum:#45333f;
  --text:#3a3a3a;
  --white:#ffffff;
}
*{box-sizing:border-box;margin:0;padding:0}
html,body{width:1200px;height:4293px;overflow:hidden}
body{font-family:'Lato',sans-serif;color:var(--text);background:var(--white);position:relative}
.btn{display:inline-block;background:var(--teal);color:var(--white);font-weight:700;border-radius:28px;text-align:center;text-decoration:none}
.section-title{font-size:44px;font-weight:700;color:var(--ink);text-align:center}
.rule{width:75px;height:5px;background:var(--teal-dark);margin:22px auto 0}
.abs{position:absolute}

/* top */
.topbar{position:absolute;left:0;top:0;width:1200px;height:58px;background:var(--mint-pale)}
.social{position:absolute;display:flex;gap:14px}
.social span{width:20px;height:20px;border-radius:50%;background:var(--ink)}
.topbar .btn{position:absolute;left:980px;top:8px;width:146px;height:40px;line-height:40px;font-size:15px}
.brand{position:absolute;left:70px;top:22px;width:160px;text-align:center}
.brand .mark{width:86px;height:86px;border-radius:50%;background:var(--teal-dark);margin:0 auto 6px}
.brand .name{font-size:25px;font-weight:900;color:var(--ink);line-height:1}
.brand .sub{font-size:12px;font-weight:900;color:var(--ink);letter-spacing:2.5px;margin-top:3px}
.nav{position:absolute;top:103px;right:73px;display:flex;gap:36px;font-size:16px;font-weight:700;color:var(--ink)}

/* hero */
.hero{position:absolute;left:0;top:168px;width:1200px;height:700px}
.hero-photo{position:absolute;inset:0;background:linear-gradient(100deg,#a9a29a 0%,#d8d3cc 35%,#cfc8c0 60%,#7f7f7c 100%)}
.hero h1{position:absolute;top:180px;width:100%;text-align:center;font-size:70px;line-height:68px;font-weight:900;color:var(--white)}
.hero .btn{position:absolute;left:510px;top:365px;width:180px;height:54px;line-height:54px;font-size:19px}
.dots{position:absolute;display:flex;gap:12px}
.dots span{width:12px;height:12px;border-radius:50%;background:var(--ink)}
.hero .dots span{background:var(--white);opacity:.8}
.hero .dots span:first-child{opacity:1}

/* overview */
.overview h2{position:absolute;left:75px;top:978px;font-size:44px;font-weight:700;color:var(--ink)}
.overview .bar{position:absolute;left:75px;top:1047px;width:75px;height:5px;background:var(--teal-dark)}
.body-copy{font-size:16px;line-height:31px;color:var(--text)}
.overview p{position:absolute;left:75px;top:1065px;width:535px}
.overview .btn{position:absolute;left:75px;top:1282px;width:179px;height:54px;line-height:54px;font-size:18px}
.emblem{position:absolute;left:663px;top:920px;width:464px;height:464px;border-radius:50%;border:26px solid var(--teal-dark);display:flex;align-items:center;justify-content:center;flex-direction:column}
.emblem .name{font-size:42px;font-weight:900;color:var(--teal-dark)}

/* cards */
.band{position:absolute;left:0;width:1200px;background:var(--mint)}
.cards{position:absolute;left:75px;display:flex;gap:30px}
.card{width:330px;text-align:center}
.card .photo{width:330px;height:200px;border-radius:10px}
.card h3{font-size:23px;font-weight:700;color:var(--ink);margin-top:20px}
.card p{font-size:16px;line-height:28px;margin:10px 18px 0}
.card .btn{width:179px;height:54px;line-height:54px;font-size:18px;margin-top:18px}

/* accommodation */
.accom-photo{position:absolute;left:75px;top:2955px;width:512px;height:355px;border-radius:8px;background:linear-gradient(90deg,#b7a497,#d8c9bf 55%,#e9e3de)}
.accom h2{position:absolute;left:616px;top:2945px;font-size:44px;font-weight:700;color:var(--ink)}
.accom .bar{position:absolute;left:616px;top:3017px;width:75px;height:5px;background:var(--teal-dark)}
.accom p{position:absolute;left:616px;top:3033px;width:520px}
.accom .btn{position:absolute;left:616px;top:3252px;width:179px;height:54px;line-height:54px;font-size:18px}

/* news */
.post{position:absolute;top:3560px;width:520px}
.post .date{font-size:15px;font-weight:700;color:var(--ink)}
.post h3{font-size:27px;line-height:35px;font-weight:700;color:var(--teal-dark);margin-top:10px}
.post p{font-size:16px;line-height:31px;margin-top:6px}

/* footer */
.footer{position:absolute;left:0;top:3892px;width:1200px;height:401px;background:var(--plum);color:var(--white)}
.footer .fbrand{position:absolute;left:75px;top:105px;width:220px;text-align:center}
.fbrand .mark{width:140px;height:140px;border-radius:50%;border:8px solid var(--white);margin:0 auto 14px}
.fbrand .name{font-size:42px;font-weight:900;line-height:1}
.fbrand .sub{font-size:18px;font-weight:900;letter-spacing:4px;margin-top:4px}
.fcol{position:absolute;top:80px;font-size:16px;line-height:33px}
.fcol h4{font-size:25px;font-weight:700;color:var(--teal);line-height:34px;margin-bottom:2px}
.fcol .social span{background:var(--teal)}
.email{width:242px;height:44px;border-radius:22px;background:var(--white);color:var(--ink);font-size:16px;line-height:44px;padding-left:18px;margin-top:14px}
.fcol .btn{width:242px;height:44px;line-height:44px;font-size:21px;margin-top:14px}
</style>
</head>
<body>

<header>
  <div class="topbar">
    <div class="social" style="left:772px;top:19px"><span></span><span></span><span></span><span></span><span></span></div>
    <a class="btn" href="#">Book Course</a>
  </div>
  <div class="brand">
    <div class="mark"></div>
    <div class="name">Veterra</div>
    <div class="sub">TRAINING CENTER</div>
  </div>
  <nav class="nav"><span>Home</span><span>About Us</span><span>Rooms</span><span>Book Course</span><span>Accommodation</span><span>Impressum</span><span>Contact Us</span></nav>
</header>

<section class="hero">
  <div class="hero-photo" role="img" aria-label="Two veterinarians in scrubs examining a small white dog on a clinic table"></div>
  <h1>Veterra<br>Training Center</h1>
  <a class="btn" href="#">Book Course</a>
  <div class="dots" style="left:560px;top:612px"><span></span><span></span><span></span><span></span></div>
  <svg class="abs" style="left:0;top:620px" width="1200" height="82" viewBox="0 0 1200 82" preserveAspectRatio="none"><path d="M0 40 Q300 0 600 60 Q900 0 1200 40 L1200 82 L0 82 Z" fill="#fff"/></svg>
</section>

<section class="overview">
  <h2>Company Overview</h2>
  <div class="bar"></div>
  <p class="body-copy">Sed ut perspiciatis unde omnis iste natus error sit voluptatem accusantium doloremque laudantium, totam rem aperiam, eaque ipsa quae ab illo inventore veritatis et quasi architecto beatae vitae dicta sunt explicabo. Nemo enim ipsam voluptatem quia voluptas sit aspernatur aut odit aut fugit, sed quia consequuntur magni dolores eos qui ratione voluptatem sequi nesciunt.</p>
  <a class="btn" href="#">Read More</a>
  <div class="emblem"><div class="name">Veterra</div></div>
</section>

<section class="courses">
  <div class="band" style="top:1458px;height:680px"></div>
  <svg class="abs" style="left:0;top:2120px" width="1200" height="60" viewBox="0 0 1200 60" preserveAspectRatio="none"><path d="M0 20 Q300 -10 600 50 Q900 -10 1200 20 L1200 0 L0 0 Z" fill="#b8ebe4"/></svg>
  <h2 class="section-title abs" style="left:0;top:1515px;width:1200px">Feature Courses</h2>
  <div class="abs" style="left:562px;top:1585px;width:75px;height:5px;background:var(--teal-dark)"></div>
  <div class="cards" style="top:1643px">
    <div class="card"><div class="photo" role="img" aria-label="Student reading an anatomy book beside an animal skeleton model" style="background:linear-gradient(90deg,#d9d8d2,#c8b9a4)"></div><h3>Course Heading</h3><p>Sed ut perspiciatis unde omnis iste natus error sit voluptatem accusantium doloremque quaerat.</p><a class="btn" href="#">Book Course</a></div>
    <div class="card"><div class="photo" role="img" aria-label="Veterinarian with stethoscope holding a dachshund" style="background:linear-gradient(90deg,#e6e4e0,#b07a4e)"></div><h3>Course Heading</h3><p>Sed ut perspiciatis unde omnis iste natus error sit voluptatem accusantium doloremque quaerat.</p><a class="btn" href="#">Book Course</a></div>
    <div class="card"><div class="photo" role="img" aria-label="Lecturer in a white coat teaching a seminar by a flipchart" style="background:linear-gradient(90deg,#c9cdc4,#dcdfd8)"></div><h3>Course Heading</h3><p>Sed ut perspiciatis unde omnis iste natus error sit voluptatem accusantium doloremque quaerat.</p><a class="btn" href="#">Book Course</a></div>
  </div>
</section>

<section class="rooms">
  <h2 class="section-title abs" style="left:0;top:2223px;width:1200px">Rooms &amp; Seating Option</h2>
  <div class="abs" style="left:562px;top:2293px;width:75px;height:5px;background:var(--teal-dark)"></div>
  <div class="cards" style="top:2352px">
    <div class="card"><div class="photo" role="img" aria-label="Veterinarian examining a small dog in a bright room" style="background:linear-gradient(90deg,#cfd3d2,#e6e2dc)"></div><h3>Room Heading</h3><p>Sed ut perspiciatis unde omnis iste natus error sit voluptatem accusantium doloremque quaerat.</p><a class="btn" href="#">More Info</a></div>
    <div class="card"><div class="photo" role="img" aria-label="Empty seminar room with blue chairs and a whiteboard" style="background:linear-gradient(180deg,#dfe2e6,#3d5f95)"></div><h3>Room Heading</h3><p>Sed ut perspiciatis unde omnis iste natus error sit voluptatem accusantium doloremque quaerat.</p><a class="btn" href="#">More Info</a></div>
    <div class="card"><div class="photo" role="img" aria-label="Classroom with desks, projector and screen" style="background:linear-gradient(180deg,#e3e5e6,#a79a8a)"></div><h3>Room Heading</h3><p>Sed ut perspiciatis unde omnis iste natus error sit voluptatem accusantium doloremque quaerat.</p><a class="btn" href="#">More Info</a></div>
  </div>
</section>

<section class="accom">
  <div class="band" style="top:2860px;height:523px"></div>
  <svg class="abs" style="left:0;top:2825px" width="1200" height="40" viewBox="0 0 1200 40" preserveAspectRatio="none"><path d="M0 38 Q300 20 600 0 Q900 20 1200 38 L1200 40 L0 40 Z" fill="#b8ebe4"/></svg>
  <div class="accom-photo" role="img" aria-label="Host greeting a traveller with a backpack in a guest room"></div>
  <h2>Accommodation</h2>
  <div class="bar"></div>
  <p class="body-copy">Sed ut perspiciatis unde omnis iste natus error sit voluptatem accusantium doloremque laudantium, totam rem aperiam, eaque ipsa quae ab illo inventore veritatis et quasi architecto beatae vitae dicta sunt explicabo. Nemo enim ipsam voluptatem quia voluptas sit aspernatur aut odit aut fugit, sed quia consequuntur magni dolores eos qui ratione voluptatem sequi nesciunt.</p>
  <a class="btn" href="#">Read More</a>
</section>

<section class="news">
  <h2 class="section-title abs" style="left:0;top:3438px;width:1200px">Impressum</h2>
  <div class="abs" style="left:562px;top:3508px;width:75px;height:5px;background:var(--teal-dark)"></div>
  <article class="post" style="left:75px"><div class="date">Oct12, 2021</div><h3>Sed ut perspiciatis unde omnis iste natus error sit voluptatem</h3><p>Sed ut perspiciatis unde omnis iste natus error sit voluptatem accusantium doloremque laudantium, totam rem aperiam, eaque ipsa quae ab illo inventore veritatis et quasi.</p></article>
  <article class="post" style="left:616px"><div class="date">Oct12, 2021</div><h3>Sed ut perspiciatis unde omnis iste natus error sit voluptatem</h3><p>Sed ut perspiciatis unde omnis iste natus error sit voluptatem accusantium doloremque laudantium, totam rem aperiam, eaque ipsa quae ab illo inventore veritatis et quasi.</p></article>
  <div class="dots" style="left:558px;top:3800px"><span></span><span></span><span></span><span></span></div>
</section>

<footer class="footer">
  <div class="fbrand"><div class="mark"></div><div class="name">Veterra</div><div class="sub">TRAINING CENTER</div></div>
  <div class="fcol" style="left:365px"><h4>Site Map</h4>Home<br>About Us<br>Rooms<br>Book Course<br>Accommodation<br>Impressum<br>Contact Us</div>
  <div class="fcol" style="left:605px;width:200px"><h4>Contact Us</h4><div style="line-height:28px">Neque porro quisquam est,qui dolorem</div><div style="margin-top:6px">1-800-555-0142</div><div>info@veterra-training.eu</div><div class="social" style="position:static;margin-top:14px"><span></span><span></span><span></span><span></span><span></span></div></div>
  <div class="fcol" style="left:885px;width:250px"><h4>Email Subscribe</h4><div style="line-height:28px;margin-top:4px">Neque porro quisquam est, qui dolorem</div><div class="email">Email Address</div><a class="btn" href="#">Subscribe</a></div>
</footer>

</body>
</html>
```